Spring 2026 Billboard - superchill with Varnel heating

Rethinking - I would like to do something with this photo - somthing about you can relaxing this summer Varnel AC can fix it or 'making AC look easy' or Making your home cool look easy

Industry/Entity Type

HVAC

```html
<!DOCTYPE html>
<html lang="en">
<head>
<meta charset="utf-8">
<title>Varnel Heating &amp; Cooling – Spring Billboard</title>
<link rel="stylesheet" href="https://fonts.googleapis.com/css2?family=Archivo:wght@700;800;900&display=swap">
<style>
  :root {
    --page-bg: #dcecf8;
    --warm-tint: #fde2c2;
    --cool-tint: #d6effb;
    --paper: #f8fbfd;
    --orange: #f7920f;
    --blue: #1b9ce0;
    --ink: #1f1f1f;
    --white: #ffffff;
    --pill-dark: #2a1f2e;
    --pill-blue: #3f8fe0;
    --pill-amber: #a4552a;
    --sun: #f8b923;
    --ice: #2d8fc4;
    --ice-light: #8fd3f2;
    --hero-blue: #2a86d6;
    --hero-cape: #e8b13a;
  }
  html, body {
    margin: 0;
    padding: 0;
    width: 946px;
    height: 1200px;
    overflow: hidden;
    background: var(--page-bg);
  }
  .billboard {
    position: absolute;
    left: 23px;
    top: 389px;
    width: 900px;
    height: 422px;
    overflow: hidden;
    background:
      radial-gradient(ellipse at 45% 50%, var(--paper) 0%, rgba(248,251,253,0) 60%),
      linear-gradient(100deg, var(--warm-tint) 0%, var(--paper) 48%, var(--cool-tint) 100%);
    box-shadow: 0 18px 36px rgba(20, 60, 110, 0.28);
    font-family: "Archivo", "Arial Black", sans-serif;
  }
  .emblem {
    position: absolute;
    z-index: 2;
    border-radius: 50%;
    background: linear-gradient(90deg, var(--sun) 0%, var(--sun) 50%, var(--ice) 50%, var(--ice-light) 100%);
  }
  .emblem--top { left: 466px; top: 0; width: 231px; height: 164px; border-radius: 0 0 50% 50%; }
  .emblem--left { left: 2px; top: 173px; width: 126px; height: 133px; }
  .emblem--corner { left: 808px; top: 356px; width: 92px; height: 66px; border-radius: 50% 50% 0 0; }
  .hero {
    position: absolute;
    z-index: 1;
    left: 140px;
    top: 176px;
    width: 300px;
    height: 246px;
    border-radius: 48% 52% 0 0 / 40% 40% 0 0;
    background: linear-gradient(110deg, var(--hero-cape) 0%, var(--hero-cape) 22%, var(--hero-blue) 40%, var(--hero-blue) 72%, var(--hero-cape) 88%);
    opacity: 0.85;
  }
  .headline {
    position: absolute;
    z-index: 3;
    margin: 0;
    font-weight: 900;
    font-size: 56px;
    line-height: 1;
    letter-spacing: -0.5px;
  }
  .headline--melting { left: 46px; top: 66px; color: var(--orange); }
  .headline--freezing { left: 98px; top: 126px; color: var(--blue); }
  .tagline {
    position: absolute;
    z-index: 3;
    left: 471px;
    top: 202px;
    width: 390px;
    margin: 0;
    color: var(--ink);
    font-weight: 800;
    font-size: 39px;
    line-height: 1.06;
    text-align: right;
    letter-spacing: -0.3px;
  }
  .web-pill {
    position: absolute;
    z-index: 3;
    left: 403px;
    top: 303px;
    width: 455px;
    height: 58px;
    border-radius: 7px;
    background: linear-gradient(100deg, var(--pill-dark) 0%, var(--pill-blue) 45%, var(--pill-blue) 60%, var(--pill-amber) 90%, var(--pill-dark) 100%);
    display: flex;
    align-items: center;
    justify-content: center;
    color: var(--white);
    font-weight: 800;
    font-size: 29px;
    letter-spacing: 0.2px;
  }
</style>
</head>
<body>
  <main class="billboard">
    <div class="emblem emblem--top" role="img" aria-label="Half sun, half snowflake emblem"></div>
    <div class="emblem emblem--left" role="img" aria-label="Half sun, half snowflake emblem"></div>
    <div class="emblem emblem--corner" role="img" aria-label="Half sun, half snowflake emblem"></div>

    <div class="hero" role="img" aria-label="Illustrated flying superhero in a blue suit and golden cape, fist forward"></div>

    <h1 class="headline headline--melting">MELTING?</h1>
    <h1 class="headline headline--freezing">FREEZING?</h1>

    <p class="tagline">WE SPEAK BOTH TEMPERATURES</p>
    <div class="web-pill">VARNELHOME.COM</div>
  </main>
</body>
</html>
```